Book cover design for my new Bankruptcy Law Book

Hi

I would like to get a unique and nice design for my new book titled: "Creditor Remedies Within Gulf Trade Statutes".

I like blue color. It will be in Arabic so I care the most about the design of the book cover and not the words on the cover as the printing company will handle the rest.

Much appreciated,

YUSUF BIN TAREQ

Colors
0692cd
33a6d7
86cae7
85abd2
3277b5
0255a3

Requirements
Must have
• Blue color
Nice to have
• pictures or shapes related to bankruptcy or insolvency

```html
<!DOCTYPE html>
<html lang="en">
<head>
<meta charset="utf-8">
<title>Creditor Remedies Within Gulf Trade Statutes — Book Cover</title>
<link rel="stylesheet" href="https://fonts.googleapis.com/css2?family=Reem+Kufi:wght@500;700&display=swap">
<style>
  :root {
    --royal-blue: #0a45f5;
    --deep-blue: #0b2fb8;
    --edge-blue: #3a8cf0;
    --paper: #eef0f6;
    --paper-shade: #cfd6e6;
    --ink: #0c0c12;
    --white: #ffffff;
  }
  html, body {
    margin: 0;
    padding: 0;
    overflow: hidden;
    background: var(--white);
  }
  .cover {
    position: relative;
    width: 800px;
    height: 1200px;
    overflow: hidden;
    font-family: "Reem Kufi", sans-serif;
    background: var(--paper);
  }
  .banknote-backdrop {
    position: absolute;
    left: 0;
    top: 238px;
    width: 800px;
    height: 962px;
    background:
      radial-gradient(ellipse at 70% 65%, rgba(150,165,200,0.45), transparent 55%),
      radial-gradient(ellipse at 20% 40%, rgba(170,185,215,0.35), transparent 50%),
      linear-gradient(160deg, #f3f4f8 0%, var(--paper) 45%, var(--paper-shade) 100%);
  }
  .title-band {
    position: absolute;
    left: 0;
    top: 0;
    width: 800px;
    height: 238px;
    background: var(--royal-blue);
  }
  .book-title {
    position: absolute;
    right: 60px;
    top: 50px;
    margin: 0;
    width: 700px;
    text-align: right;
    color: var(--white);
    font-weight: 700;
    font-size: 50px;
    line-height: 78px;
  }
  .subtitle {
    position: absolute;
    right: 85px;
    top: 254px;
    margin: 0;
    text-align: right;
    color: var(--ink);
    font-weight: 500;
    font-size: 26px;
    line-height: 48px;
    direction: rtl;
  }
  .decline-arrow {
    position: absolute;
    left: 0;
    top: 0;
    width: 800px;
    height: 1200px;
  }
  .author {
    position: absolute;
    right: 275px;
    top: 1105px;
    margin: 0;
    color: var(--ink);
    font-weight: 700;
    font-size: 24px;
    letter-spacing: 1px;
  }
</style>
</head>
<body>
  <div class="cover">
    <div class="banknote-backdrop" role="img" aria-label="Faded photograph of scattered 500 riyal banknotes"></div>

    <svg class="decline-arrow" viewBox="0 0 800 1200" aria-hidden="true">
      <polygon class="arrow-tail" fill="var(--deep-blue)" points="0,238 130,238 400,393 245,433 0,338"/>
      <polygon class="arrow-edge" fill="var(--edge-blue)" points="0,338 245,433 233,436 0,348"/>
      <polygon class="arrow-edge" fill="var(--edge-blue)" points="233,436 245,433 430,848 420,850"/>
      <polygon class="arrow-shaft" fill="var(--royal-blue)" points="245,433 400,393 485,840 585,830 525,1060 298,855 430,848"/>
      <polygon class="arrow-edge" fill="var(--edge-blue)" points="298,855 310,852 525,1060"/>
    </svg>

    <header class="title-band">
      <h1 class="book-title">Creditor Remedies Within<br>Gulf Trade Statutes</h1>
    </header>

    <p class="subtitle">بثاثاثآت ثإإبب تب<br>آأثآتتتأ آت جاب</p>

    <p class="author">YUSUF BIN TAREQ</p>
  </div>
</body>
</html>
```